Logo and Card design for KRV Home Solutions LLC

I need an edgier logo and business card designs. Current logo attached. I like the colors below. I would like the logo to incorporate a home in the design.
Title = Principal-Acquisitions
Email:KRVHOMESOLUTIONS@fernmail.example
555-214-0937
facebook
IG
2 sided business card with the front being contact info a slogan about selling a home fast. The back incorporating What we do. Buy houses, land, or commercial property as is. We find solutions to make the process of selling simple and fair.

Target Market(s)

Motivated house sellers.

Industry/Entity Type

Business

Contact Information for Business Card

Who we are: We are a Faith based Real Estate Investment Company. We pay cash for homes in any condition and can close quick. Whatever the reason you need to sell fast, we can help. We believe in creating win-win solutions to help you in your time of need. We care! We can help!

Logo Text

KRV Home Solutions LLC

Font styles to use
Sans Serif

Colors
33a6d7
0355a3
85abd2
cee9f5
9d9d9d
b2b2b2
ffffff

Requirements
Must have
• Old logo attached. I want something edgier.
• Company name, phone number, description on the back of what we can do. Pay all cash. Buy in as is condition. No fees,Commisions or closing costs.Close quick. No hassles with solutions to meet your unique situation.
• Call today for an offer within 24 hours.

```html
<!DOCTYPE html>
<html lang="en">
<head>
<meta charset="utf-8">
<title>KRV Home Solutions – Business Card</title>
<link href="https://fonts.googleapis.com/css2?family=Source+Sans+3:wght@400;600;700&display=swap" rel="stylesheet">
<style>
  :root {
    --backdrop: #a9a9a9;
    --brand-blue: #1458a3;
    --card-white: #ffffff;
    --ink: #2b2b2b;
    --rule: #b2b2b2;
  }
  html, body { margin: 0; padding: 0; overflow: hidden; }
  body {
    width: 1200px; height: 900px;
    background: var(--backdrop);
    position: relative;
    font-family: "Source Sans 3", sans-serif;
  }
  .card {
    position: absolute; top: 170px;
    width: 347px; height: 561px;
    box-shadow: 3px 4px 6px rgba(0,0,0,0.35);
    overflow: hidden;
  }
  .card-front { left: 259px; background: var(--card-white); text-align: center; }
  .card-back { left: 631px; background: var(--card-white); }

  .wordmark {
    position: absolute; left: 0; right: 0; top: 118px;
    margin: 0; color: var(--brand-blue);
    font-size: 38px; font-weight: 700; line-height: 42px; letter-spacing: 0.5px;
  }
  .holder-name {
    position: absolute; left: 0; right: 0; top: 357px; margin: 0;
    color: var(--brand-blue); font-size: 27px; font-weight: 700;
  }
  .holder-title {
    position: absolute; left: 0; right: 0; top: 391px; margin: 0;
    color: var(--ink); font-size: 17px;
  }
  .divider {
    position: absolute; left: 113px; width: 160px; height: 1px; background: var(--rule);
  }
  .divider-top { top: 422px; }
  .divider-bottom { top: 493px; }
  .contact-list {
    position: absolute; left: 0; right: 0; top: 433px; margin: 0; padding: 0;
    list-style: none; color: var(--ink); font-size: 17px; line-height: 23px;
  }
  .contact-list b { color: var(--brand-blue); font-weight: 700; }
  .social-links {
    position: absolute; top: 505px; left: 0; right: 0;
    display: flex; justify-content: center; gap: 15px;
  }
  .social-dot {
    width: 33px; height: 33px; border-radius: 50%;
    border: 2px solid var(--brand-blue); box-sizing: border-box;
  }

  .services-panel {
    position: absolute; left: 0; top: 0; width: 287px; height: 561px;
    background: var(--brand-blue);
  }
  .services-list {
    position: absolute; width: 561px; height: 287px;
    left: -137px; top: 137px;
    transform: rotate(-90deg);
    margin: 0; padding: 58px 0 0 86px; box-sizing: border-box;
    list-style: none; color: var(--card-white);
    font-size: 17px; font-weight: 600; line-height: 29.5px;
  }
  .services-list li::before { content: "\2605"; font-size: 11px; margin-right: 9px; vertical-align: 2px; }
  .services-list .wrap { display: block; padding-left: 20px; }
  .callout-strip {
    position: absolute; left: 287px; top: 0; width: 60px; height: 561px;
  }
  .callout {
    position: absolute; width: 561px; height: 60px;
    left: -250px; top: 250px;
    transform: rotate(-90deg);
    margin: 0; text-align: center; line-height: 60px;
    color: var(--brand-blue); font-size: 21px; font-weight: 700; letter-spacing: 0.3px;
  }
</style>
</head>
<body>
  <section class="card card-front">
    <h1 class="wordmark">KRV HOME<br>SOLUTIONS</h1>
    <h2 class="holder-name">DANA WHITFIELD</h2>
    <p class="holder-title">Managing Director</p>
    <div class="divider divider-top"></div>
    <ul class="contact-list">
      <li><b>P</b>: 555-214-0937</li>
      <li><b>E</b>: krvhomesolutions@fernmail.example</li>
    </ul>
    <div class="divider divider-bottom"></div>
    <div class="social-links">
      <span class="social-dot" aria-label="Social profile"></span>
      <span class="social-dot" aria-label="Social profile"></span>
    </div>
  </section>

  <section class="card card-back">
    <div class="services-panel">
      <ul class="services-list">
        <li>Buy houses, land or commercial property as is.</li>
        <li>Pay all cash.</li>
        <li>Buy in as is condition.</li>
        <li>No fees, commisions or closing costs.</li>
        <li>Close quick. No hassles with solutions<span class="wrap">to meet your unique situation.</span></li>
      </ul>
    </div>
    <div class="callout-strip">
      <p class="callout">CALL TODAY FOR AN OFFER WITHIN 24 HOURS.</p>
    </div>
  </section>
</body>
</html>
```